Kelvaro.ch is looking for business card letterhead and envelope C5 with WOW effect

We need a strong business card for our company Kelvaro.ch, logo is available. You want a black or dark background on which the logo Stark r% 26 # 252; appears. Letterhead and envelope in C5 format should be in a similar design, but does not have to be We need a strong business card for our company Kelvaro.ch, logo is available. A black or dark background is desired, on which the logo Stark comes across. The letterhead and the envelope in C5 format should have a similar design.

Target Market(s)

Private customers as well as entrepreneurs

Contact Information for Business Card

E-mail: info@kelvaro-example.ch
Web.www.Kelvaro-example.ch
Tel: +41 ( 0 ) 79 482 6037
Adresse:
Lindenweg 14
9406 Tarnbach

Hier kann man Icons verwenden für Email,Tel und Adressse

Font styles to use
Other font styles liked:
• Dubai,bold

Colors

Designer to choose colors to be used in the design.

Requirements
Must have
• WOW effect
Nice to have
• R% 26 # 252; back business card with our service listings. - VEHICLE LABELING - SHOP WINDOW LABELING - STICKERS AND MUCH MORE ... in red color

```html
<!DOCTYPE html>
<html lang="en">
<head>
<meta charset="utf-8">
<title>Kelvaro.ch business card</title>
<link rel="stylesheet" href="https://fonts.googleapis.com/css2?family=Titillium+Web:wght@400;600;700&display=swap">
<style>
  :root {
    --backdrop: #9a9a9a;
    --card: #1f1f1f;
    --accent: #ffcc1a;
    --muted: #c9c9c9;
    --shadow: rgba(0,0,0,0.35);
  }
  * { margin: 0; padding: 0; box-sizing: border-box; }
  html, body { width: 1200px; height: 965px; overflow: hidden; }
  body {
    background: var(--backdrop);
    font-family: "Titillium Web", sans-serif;
    position: relative;
  }
  .card {
    position: absolute;
    left: 278px;
    width: 648px;
    height: 368px;
    background: var(--card);
    border-radius: 26px;
    box-shadow: 0 14px 22px var(--shadow);
    overflow: hidden;
  }
  .card--front { top: 98px; }
  .card--back { top: 504px; }

  .pattern-area {
    position: absolute;
    border-radius: 18px;
    background: linear-gradient(135deg, rgba(255,204,26,0.85) 0%, rgba(255,204,26,0.45) 55%, rgba(255,204,26,0.15) 100%);
  }
  .card--front .pattern-area { left: 24px; top: 46px; width: 222px; height: 276px; }
  .card--back .pattern-area { left: 24px; top: 22px; width: 273px; height: 324px; }

  .brand-name {
    position: absolute;
    right: 26px;
    top: 156px;
    font-size: 60px;
    font-weight: 700;
    line-height: 1;
    letter-spacing: 0;
    color: var(--accent);
    white-space: nowrap;
  }
  .services {
    position: absolute;
    right: 26px;
    top: 253px;
    list-style: none;
    text-align: right;
  }
  .services li {
    display: flex;
    justify-content: flex-end;
    align-items: center;
    gap: 10px;
    height: 23.5px;
    font-size: 16px;
    font-weight: 600;
    color: var(--accent);
    text-transform: uppercase;
    white-space: nowrap;
  }
  .services svg { width: 14px; height: 14px; }

  .person {
    position: absolute;
    right: 30px;
    top: 28px;
    text-align: right;
  }
  .person__name {
    font-size: 22px;
    font-weight: 700;
    line-height: 1.2;
    color: var(--accent);
    letter-spacing: 0.3px;
  }
  .person__role {
    font-size: 15px;
    font-weight: 400;
    color: var(--muted);
    line-height: 1.3;
  }
  .address {
    position: absolute;
    right: 30px;
    top: 195px;
    text-align: right;
    font-style: normal;
    font-size: 15.5px;
    line-height: 23px;
    color: var(--muted);
  }
  .divider {
    position: absolute;
    right: 31px;
    top: 249px;
    width: 54px;
    height: 2px;
    background: var(--accent);
  }
  .contacts {
    position: absolute;
    right: 30px;
    top: 273px;
    list-style: none;
  }
  .contacts li {
    display: flex;
    justify-content: flex-end;
    align-items: center;
    gap: 10px;
    height: 24px;
    font-size: 15.5px;
    color: var(--muted);
    white-space: nowrap;
  }
  .contacts svg { width: 16px; height: 16px; }
</style>
</head>
<body>

<section class="card card--front">
  <div class="pattern-area" role="img" aria-label="Yellow honeycomb pattern of filled and outlined hexagons"></div>
  <div class="brand-name">KELVARO.CH</div>
  <ul class="services">
    <li>Vehicle labeling <svg viewBox="0 0 14 14"><polygon points="3.5,1 10.5,1 14,7 10.5,13 3.5,13 0,7" fill="var(--accent)"/></svg></li>
    <li>Shop window labeling <svg viewBox="0 0 14 14"><polygon points="3.5,1 10.5,1 14,7 10.5,13 3.5,13 0,7" fill="var(--accent)"/></svg></li>
    <li>Stickers and much more <svg viewBox="0 0 14 14"><polygon points="3.5,1 10.5,1 14,7 10.5,13 3.5,13 0,7" fill="var(--accent)"/></svg></li>
  </ul>
</section>

<section class="card card--back">
  <div class="pattern-area" role="img" aria-label="Yellow honeycomb pattern of filled and outlined hexagons"></div>
  <div class="person">
    <div class="person__name">ADRIAN VOGEL</div>
    <div class="person__role">DIRECTOR</div>
  </div>
  <address class="address">
    Lindenweg 14<br>
    9406 Tarnbach
  </address>
  <div class="divider"></div>
  <ul class="contacts">
    <li>+41 ( 0 ) 79 482 6037
      <svg viewBox="0 0 16 16"><path d="M3 1.5l2.5 0 1.2 3.2-1.6 1.2c.8 1.8 2.2 3.2 4 4l1.2-1.6 3.2 1.2v2.5c0 .8-.7 1.5-1.5 1.5C6.5 13.5 2.5 9.5 1.5 3 1.5 2.2 2.2 1.5 3 1.5z" fill="var(--accent)"/><path d="M10 2a4 4 0 0 1 4 4M10 4.3a1.8 1.8 0 0 1 1.7 1.7" stroke="var(--accent)" stroke-width="1.3" fill="none"/></svg>
    </li>
    <li>info@kelvaro-example.ch
      <svg viewBox="0 0 16 16"><rect x="0.5" y="3" width="15" height="10" rx="1" fill="var(--accent)"/><path d="M1 3.5l7 5.5 7-5.5" stroke="var(--card)" stroke-width="1.3" fill="none"/></svg>
    </li>
    <li>www.Kelvaro-example.ch
      <svg viewBox="0 0 16 16"><circle cx="8" cy="8" r="7.2" fill="var(--accent)"/><path d="M4 4.5c1.5.5 2 1.5 1.3 2.6-.6 1 .3 2 1.5 2.2.8.2.6 1.8-.2 2.8M10 2.5c-.8 1.2.2 2 1.2 2.3 1 .3 1.8 1.5 1 2.8" stroke="var(--card)" stroke-width="1.3" fill="none"/></svg>
    </li>
  </ul>
</section>

</body>
</html>
```